I have a logo and need to design the business card and stationery.
Updates

The uploaded logo image named as GREYMARSH CONSTRUCTION which is to be replaced to GREYMARSH CONTRACTS. Kindly add below details and submit the designs- Company name- Greymarsh Engineering Contracts LLP Name & Post- Kelvan Joshi (Designated Partner) Address- Block No.317, Wing C, Tulvo Trade Court, Manek Pural Road, Ruparel Industrial Estate, Goregaon(E), Mumbai - 400 063 Contact- +91 97415 60382 Email- kelvanjoshi@mailbrook.example Website- www.greymarshcontracts.example Contact for Letterhead- +91-22-28754193

Hi Tovin Rahul, We are liking your Design #28860835. We have suggested some changes which are mentioned in feedback. Kindly revert with it asap to finalize this design.

Colors

Designer to choose colors to be used in the design.

```html
<!DOCTYPE html>
<html lang="en">
<head>
<meta charset="utf-8">
<title>Greymarsh Contracts – Business Card</title>
<link rel="stylesheet" href="https://fonts.googleapis.com/css2?family=Archivo+Black&family=Cormorant+SC:wght@700&display=swap">
<style>
  :root {
    --backdrop: #262626;
    --card: #ececec;
    --ink: #2b2b2b;
    --ink-soft: #555555;
    --rule: #9a9a9a;
    --back-light: #f6f6f6;
    --back-mid: #e4e4e4;
    --back-dark: #cdcdcd;
  }
  * { margin: 0; padding: 0; box-sizing: border-box; }
  html, body { width: 1200px; height: 1108px; overflow: hidden; }
  body {
    background: var(--backdrop);
    display: flex;
    align-items: center;
    justify-content: center;
    gap: 70px;
  }
  .card {
    width: 400px;
    height: 680px;
    border-radius: 22px;
    background: var(--card);
    box-shadow: 0 14px 30px rgba(0,0,0,.45);
    position: relative;
    overflow: hidden;
  }
  .card-front {
    display: flex;
    flex-direction: column;
    align-items: center;
    padding-top: 110px;
    color: var(--ink);
  }
  .brand {
    display: flex;
    flex-direction: column;
    align-items: center;
    gap: 14px;
  }
  .brand-square {
    width: 64px; height: 64px;
    background: var(--ink);
  }
  .brand-name {
    font-family: "Archivo Black", sans-serif;
    font-size: 30px;
    letter-spacing: 0.5px;
    line-height: 1.1;
    text-align: center;
    color: var(--ink);
  }
  .person {
    margin-top: 96px;
    text-align: center;
  }
  .person-name {
    font-family: "Archivo Black", sans-serif;
    font-size: 21px;
    letter-spacing: 1px;
  }
  .person-title {
    font-family: "Cormorant SC", serif;
    font-weight: 700;
    font-size: 19px;
    color: var(--ink-soft);
    margin-top: 2px;
  }
  .divider {
    width: 250px;
    height: 1px;
    background: var(--rule);
    margin: 12px 0;
  }
  .contact-icons {
    display: flex;
    gap: 6px;
    margin-bottom: 8px;
  }
  .contact-icons svg { width: 26px; height: 26px; }
  .contact-lines {
    font-family: "Cormorant SC", serif;
    font-weight: 700;
    font-size: 18px;
    line-height: 1.35;
    text-align: center;
  }
  .address {
    font-family: "Cormorant SC", serif;
    font-weight: 700;
    font-size: 16px;
    line-height: 1.3;
    text-align: center;
    width: 320px;
  }
  .card-back .pattern-fill {
    position: absolute;
    inset: 0;
    background: linear-gradient(160deg, var(--back-light) 0%, var(--back-mid) 50%, var(--back-dark) 100%);
  }
  .back-brand {
    position: absolute;
    left: 0; right: 0;
    bottom: 150px;
    text-align: center;
    font-family: "Archivo Black", sans-serif;
    font-size: 20px;
    letter-spacing: 0.5px;
    color: var(--ink);
  }
</style>
</head>
<body>
  <article class="card card-front">
    <div class="brand">
      <span class="brand-square"></span>
      <span class="brand-name">GREYMARSH<br>CONTRACTS</span>
    </div>

    <div class="person">
      <div class="person-name">KELVAN JOSHI</div>
      <div class="person-title">Designated Partner</div>
    </div>

    <div class="divider"></div>

    <div class="contact-icons">
      <svg viewBox="0 0 26 26" aria-label="Phone">
        <rect width="26" height="26" rx="4" fill="#2b2b2b"/>
        <path d="M8 7c1-1 2-1 3 0l1 2c0 1-1 1-1 2 1 2 2 3 4 4 1 0 1-1 2-1l2 1c1 1 1 2 0 3-2 2-5 1-8-2S6 9 8 7z" fill="#ececec"/>
      </svg>
      <svg viewBox="0 0 26 26" aria-label="Email">
        <rect width="26" height="26" rx="4" fill="#2b2b2b"/>
        <rect x="6" y="8" width="14" height="10" fill="none" stroke="#ececec" stroke-width="1.6"/>
        <path d="M6 8l7 6 7-6" fill="none" stroke="#ececec" stroke-width="1.6"/>
      </svg>
      <svg viewBox="0 0 26 26" aria-label="Website">
        <rect width="26" height="26" rx="4" fill="#2b2b2b"/>
        <circle cx="13" cy="13" r="7" fill="none" stroke="#ececec" stroke-width="1.6"/>
        <path d="M6 13h14M13 6c-3 4-3 10 0 14M13 6c3 4 3 10 0 14" fill="none" stroke="#ececec" stroke-width="1.2"/>
      </svg>
    </div>

    <div class="contact-lines">
      +91 97415 60382<br>
      kelvanjoshi@mailbrook.example<br>
      www.greymarshcontracts.example
    </div>

    <div class="divider"></div>

    <div class="address">
      Block No.317, Wing C, Tulvo Trade Court, Manek Pural Road, Ruparel Industrial Estate, Goregaon(E), Mumbai - 400 063
    </div>
  </article>

  <article class="card card-back">
    <div class="pattern-fill" role="img" aria-label="Embossed repeating brand pattern covering the card back"></div>
    <div class="back-brand">GREYMARSH CONTRACTS</div>
  </article>
</body>
</html>
```